App Design - Career Prep Pal

We require an App Design for our new App called 'Hiring Helper'. This app is essentially an assistant to help Users prepare for job interviews, to help them get hired. <br/><br/>Users who download the App can view common Questions and Answers, save their favourite responses and also view common Interview Tips. <br/><br/>The vision for our App is for Users who are preparing for an interview (1 week before, 1 day before, even 1 hour before), are able to download, view and educate themselves on common questions and responses, and then be confident to land the job. <br/><br/>Our team has developed wireframes to help highlight what each screen should do and include. Please see attached document, which also highlights key requirements for the experience. Feel free to add/remove/edit what you see on these wireframes. Our preference is that you use Adobe XD please.<br/><br/>In terms of design guidelines, we want the experience to be simple, intuitive and 'memorable' to help Users to remember the questions/responses when they are in the interview. <br/><br/>The final design should communicate 'neat and clean professionalism'; we like the design of: jobvista net au<br/><br/>Thank you for reading! Good luck !

Target Market(s)

Professional job seekers

Font styles to use
Sans Serif

Colors

Designer to choose colors to be used in the design.

Requirements
Must have
• Please see my PixelGuild_UX file that I have uploaded
Nice to have
• Could you also please include some ideas on how we can incorporate Advertising into the app screens

```html
<!DOCTYPE html>
<html lang="en">
<head>
<meta charset="utf-8">
<title>Hiring Helper – App Screens</title>
<link href="https://fonts.googleapis.com/css2?family=Mulish:wght@400;600;700&display=swap" rel="stylesheet">
<style>
:root{
  --stage:#2b2b2b;
  --paper:#f9f8f5;
  --lilac:#e7e4ef;
  --white:#ffffff;
  --ink:#222326;
  --slate:#4b5666;
  --blue-a:#1f9cf1;
  --blue-b:#4b69de;
  --violet-a:#9699f8;
  --violet-b:#696ddf;
  --coral-a:#f8a6a6;
  --coral-b:#ec6c70;
  --item-blue:#2d86ea;
  --item-grey:#e6e6e6;
  --text-soft:#3b3b3f;
}
*{box-sizing:border-box;margin:0;padding:0}
html,body{width:1200px;height:2350px;overflow:hidden;background:var(--stage);font-family:"Mulish",sans-serif;color:var(--ink)}
.screen{position:absolute;width:553px;height:1125px;overflow:hidden}
.screen--splash{left:41px;top:42px;background:var(--paper)}
.screen--menu{left:611px;top:42px;background:var(--paper)}
.screen--categories{left:41px;top:1184px;background:var(--lilac)}
.screen--questions{left:611px;top:1184px;background:var(--lilac)}
.abs{position:absolute}
.brand{display:flex;align-items:center;gap:8px;font-weight:600;white-space:nowrap}
.brand__mark{display:inline-block;background:var(--ink);border-radius:2px}
.splash-title{left:0;width:553px;top:88px;justify-content:center;font-size:56px}
.splash-title .brand__mark{width:36px;height:38px}
.tagline{left:26px;top:182px;width:501px;height:146px;background:linear-gradient(180deg,var(--blue-a),var(--blue-b));color:var(--white);font-size:22px;line-height:35px;text-align:center;padding:20px 24px;font-weight:600;box-shadow:0 2px 4px rgba(0,0,0,.15)}
.hero{left:0;width:553px;bottom:0;background:linear-gradient(180deg,rgba(249,248,245,0) 0%,#e9dcd4 30%,#b98f88 55%,#c6a39a 80%,#d8ccc4 100%)}
.screen--splash .hero{top:380px}
.screen--menu .hero{top:520px}
.bar-title{left:0;width:553px;top:22px;justify-content:center;font-size:27px}
.bar-title .brand__mark{width:18px;height:20px}
.menu-btn{left:26px;width:500px;height:130px;display:flex;align-items:center;color:var(--white);font-weight:700;font-size:37px;line-height:43px;text-transform:uppercase}
.menu-btn__icon{width:104px;height:104px;border-radius:50%;background:var(--white);margin:0 16px 0 16px;flex:none;display:flex;align-items:center;justify-content:center}
.menu-btn--questions{top:72px;background:linear-gradient(180deg,var(--blue-a),var(--blue-b))}
.menu-btn--portfolio{top:222px;background:linear-gradient(180deg,var(--violet-a),var(--violet-b))}
.menu-btn--tips{top:363px;background:linear-gradient(180deg,var(--coral-a),var(--coral-b))}
.back{left:26px;top:18px;width:86px;height:35px;background:var(--white);border-radius:2px;display:flex;align-items:center;gap:7px;padding-left:9px;font-size:18px;color:#666}
.back__dot{width:16px;height:16px;border-radius:50%;background:#8a8a8e;display:flex;align-items:center;justify-content:center}
.inner-title{left:160px;top:18px;font-size:27px}
.inner-title .brand__mark{width:18px;height:20px}
.card{left:26px;top:73px;width:500px;height:1017px;background:var(--white)}
.card__heading{left:0;width:553px;top:124px;text-align:center;font-size:20px}
.hint{left:51px;top:218px;font-size:16px}
.cat{left:52px;width:449px;height:129px;background:var(--slate);color:var(--white);font-size:41px;display:flex;align-items:center}
.cat__icon{width:156px;display:flex;justify-content:center}
.cat--1{top:272px}.cat--2{top:445px}.cat--3{top:617px}.cat--4{top:790px}
.view-all{left:208px;top:953px;width:138px;height:61px;background:linear-gradient(180deg,#f6a0a0,#ef7a7c);color:var(--white);font-size:26px;display:flex;align-items:center;justify-content:center}
.section-band{left:52px;top:222px;width:449px;height:69px;background:var(--slate);color:var(--white);font-size:40px;display:flex;align-items:center;justify-content:center}
.q{left:52px;width:449px;display:flex;align-items:center;padding:0 26px 0 18px;font-size:16.5px;line-height:26px;color:var(--text-soft);background:var(--item-grey)}
.q__num{width:28px;flex:none;align-self:flex-start}
.q--1{top:328px;height:129px;background:var(--item-blue);color:var(--white)}
.q--2{top:485px;height:129px}
.q--3{top:642px;height:103px}
.q--4{top:773px;height:103px}
.q--5{top:904px;height:102px}
</style>
</head>
<body>

<section class="screen screen--splash">
  <div class="abs brand splash-title"><span class="brand__mark"></span>Hiring Helper</div>
  <p class="abs tagline">Your guide to the most common interview question, and the best response to help you get hired.</p>
  <div class="abs hero" role="img" aria-label="Photo of a smiling job seeker in a checked shirt celebrating while reading his phone"></div>
</section>

<section class="screen screen--menu">
  <div class="abs brand bar-title"><span class="brand__mark"></span>Hiring Helper</div>
  <a class="abs menu-btn menu-btn--questions">
    <span class="menu-btn__icon"><svg width="66" height="66" viewBox="0 0 66 66" fill="none" stroke="#3b82e8" stroke-width="2"><circle cx="33" cy="33" r="30"/><path d="M24 25a9 9 0 1 1 13 8c-3 2-4 3-4 7"/><circle cx="33" cy="47" r="1.5" fill="#3b82e8"/></svg></span>
    <span>View questions &amp;<br>responses</span>
  </a>
  <a class="abs menu-btn menu-btn--portfolio">
    <span class="menu-btn__icon"><svg width="66" height="66" viewBox="0 0 66 66" fill="none" stroke="#6d72e0" stroke-width="2"><path d="M14 18h12l4 5h22v30H14z"/><path d="M14 53l8-22h38l-8 22"/><path d="M22 14h26v9M26 26h20M26 30h16"/></svg></span>
    <span>My question<br>portfolio</span>
  </a>
  <a class="abs menu-btn menu-btn--tips">
    <span class="menu-btn__icon"><svg width="66" height="66" viewBox="0 0 66 66" fill="none" stroke="#ec6c70" stroke-width="2"><circle cx="33" cy="33" r="30"/><circle cx="33" cy="20" r="3"/><rect x="30" y="28" width="6" height="22" rx="3"/></svg></span>
    <span>Interview tips</span>
  </a>
  <div class="abs hero" role="img" aria-label="Photo of a smiling job seeker in a checked shirt celebrating while reading his phone"></div>
</section>

<section class="screen screen--categories">
  <div class="abs back"><span class="back__dot"><svg width="8" height="8" viewBox="0 0 8 8"><path d="M5.5 1L2.5 4l3 3" stroke="#fff" stroke-width="1.6" fill="none"/></svg></span>Back</div>
  <div class="abs brand inner-title"><span class="brand__mark"></span>Hiring Helper</div>
  <div class="abs card"></div>
  <h2 class="abs card__heading" style="font-weight:400">View Questions and Responses</h2>
  <p class="abs hint">Select your question category</p>
  <a class="abs cat cat--1"><span class="cat__icon"><svg width="64" height="52" viewBox="0 0 64 52" fill="none" stroke="#fff" stroke-width="1.6"><path d="M4 22l14-10 10 4 10-4 16 10-18 16c-3 3-6 3-9 0L4 22z"/><path d="M44 10L60 0"/></svg></span>Behavioural</a>
  <a class="abs cat cat--2"><span class="cat__icon"><svg width="62" height="62" viewBox="0 0 62 62" fill="none" stroke="#fff" stroke-width="1.6"><rect x="18" y="4" width="26" height="16"/><path d="M6 28h50M12 28v30M50 28v30M4 40h12v18M58 40H46v18"/></svg></span>Situational</a>
  <a class="abs cat cat--3"><span class="cat__icon"><svg width="52" height="62" viewBox="0 0 52 62" fill="none" stroke="#fff" stroke-width="1.6"><path d="M8 58V40c0-8 8-12 14-8l10-24c3-6 12-4 12 4v28c0 10-8 18-20 18z"/></svg></span>Motivational</a>
  <a class="abs cat cat--4"><span class="cat__icon"><svg width="62" height="62" viewBox="0 0 62 62" fill="none" stroke="#fff" stroke-width="1.6"><circle cx="31" cy="18" r="10"/><path d="M12 50c0-12 8-18 19-18s19 6 19 18M4 58h54"/><rect x="20" y="40" width="22" height="18"/></svg></span>Technical</a>
  <a class="abs view-all">View All</a>
</section>

<section class="screen screen--questions">
  <div class="abs back"><span class="back__dot"><svg width="8" height="8" viewBox="0 0 8 8"><path d="M5.5 1L2.5 4l3 3" stroke="#fff" stroke-width="1.6" fill="none"/></svg></span>Back</div>
  <div class="abs brand inner-title"><span class="brand__mark"></span>Hiring Helper</div>
  <div class="abs card"></div>
  <h2 class="abs card__heading" style="font-weight:400">View Questions and Responses</h2>
  <div class="abs section-band">Behavioural</div>
  <div class="abs q q--1"><span class="q__num">1.</span><span>Give me an example of a new idea or initiative you have suggested to your manager How did you implement this idea?</span></div>
  <div class="abs q q--2"><span class="q__num">2.</span><span>Give me an example of a time when you made a mistake or didn't deliver on expectations, what happened? What did you learn?</span></div>
  <div class="abs q q--3"><span class="q__num">3.</span><span>How would your colleagues describe you in three words?</span></div>
  <div class="abs q q--4"><span class="q__num">4.</span><span>What parts of your current role frustrate you?</span></div>
  <div class="abs q q--5"><span class="q__num">5.</span><span>What steps would you take to make an important decision on the job?</span></div>
</section>

</body>
</html>
```